Debt Collection Website Design! We are the solution for landlords to get paid what they are owed.

We are a 3rd party debt collection company that specializes in Residential and Commercial real estate debt collection. We help landlords recover money from past residents by being fair, friendly and aggressive. We also collect/buy/sell/trade civil judgments won resulting from anything from automobile accidents to evictions to a pet zebra getting stolen. We buy single judgments to large portfolios, we also collect judgments for a nominal fee.

I would like a new, modern, easy to navigate website. A spot that we can post news stories or updated information about our company. I have included our company logo that must be on the top of the page. Feel free to ask any questions that will help get the process going.

Target Market(s)

Landlords, small to large apartment complex. Real estate services and lawyers.

Industry/Entity Type

Real Estate

Number of Pages Required

3 page

Requirements
Must have
• Company logo which has been attached. A page where we can explain the collection process, fees and placement. A page where we can explain judgments, collection vs. selling, placement form. I am open to any font/designs and willing to work with anyone.
Nice to have
• Nice to have a spot on the homepage to place news articles about ourselves and our industry.
Should not have
• I don't want it over crowded. Simple, sleek and easy to navigate is best. No gavels on any of the pages. It cannot look legal, say/show anything that we use legal powers to collect. We are not a law office, we don't practice law, we are 3rd party debt collection agency.

```html
<!DOCTYPE html>
<html lang="en">
<head>
<meta charset="utf-8">
<title>Varden Recovery, LLC</title>
<link rel="stylesheet" href="https://fonts.googleapis.com/css2?family=Oswald:wght@700&family=Roboto:wght@400;500;700&family=Open+Sans:wght@400;600&family=Cinzel:wght@400&display=swap">
<style>
:root{
  --navy:#0d2b75;
  --navy-dark:#0a2260;
  --home-box:#1b1f2b;
  --ink:#2b2b2b;
  --muted:#555;
  --line:#e6e6e6;
  --band:#f3f3f3;
  --badge:#b5b5b5;
  --white:#fff;
}
*{box-sizing:border-box;margin:0;padding:0}
html,body{width:801px;height:1200px;overflow:hidden;background:var(--white)}
body{position:relative;font-family:"Open Sans",sans-serif;color:var(--ink)}
.abs{position:absolute}

/* header */
.brand{left:66px;top:21px;height:51px;display:flex;align-items:center;gap:10px}
.brand-mark{width:24px;height:24px;background:var(--navy)}
.brand-name{font-family:"Cinzel",serif;color:var(--navy);font-size:25px;line-height:1;letter-spacing:.5px}
.contact{right:66px;top:32px;text-align:left;display:flex;gap:18px;align-items:center}
.contact-text{font-size:10px;line-height:17px;color:#333}
.contact-text .toll{color:var(--navy);font-weight:600;font-size:10.5px}

/* nav */
.nav{left:0;top:91px;width:801px;height:40px;background:var(--navy)}
.nav-home{left:66px;top:0;width:54px;height:40px;background:var(--home-box);display:flex;align-items:center;justify-content:center}
.nav-item{top:0;line-height:40px;color:var(--white);font-family:"Roboto",sans-serif;font-size:9.6px;letter-spacing:.2px}

/* hero */
.hero{left:66px;top:152px;width:669px;height:352px;background:linear-gradient(100deg,#e9eef2 0%,#d7dfe6 40%,#b9c2cc 70%,#8c96a2 100%);box-shadow:0 10px 14px -8px rgba(0,0,0,.45)}
.hero-title{left:95px;top:280px;font-family:"Oswald",sans-serif;font-weight:700;color:var(--navy);font-size:44px;line-height:52px;letter-spacing:-.5px}
.hero-arrow{top:393px;width:20px;height:20px;border-radius:50%;background:#4a4a4a;display:flex;align-items:center;justify-content:center}

/* welcome */
.welcome{left:66px;top:528px;width:669px;text-align:center}
.welcome h1{font-family:"Roboto",sans-serif;font-weight:400;font-size:21px;color:var(--ink)}
.welcome h1 strong{color:var(--navy);font-weight:700}
.welcome p{margin:14px auto 0;width:600px;font-size:7.4px;line-height:13.6px;color:#444}

/* services */
.service{top:631px;width:206px}
.service-img{width:206px;height:122px}
.service h2{margin-top:14px;font-family:"Roboto",sans-serif;font-weight:400;font-size:10.5px;color:var(--ink)}
.service p{margin-top:6px;font-size:7.2px;line-height:13.6px;color:#444}
.read-more{display:inline-block;margin-top:6px;font-size:10px;color:var(--navy);text-decoration:underline}

.divider{left:66px;top:874px;width:669px;height:1px;background:var(--line)}

/* news */
.news-heading{left:65px;top:894px;font-family:"Roboto",sans-serif;font-weight:400;font-size:13.5px;color:var(--ink)}
.news-img{top:926px;width:124px;height:109px}
.news-body{top:922px;width:180px}
.news-body h3{font-family:"Roboto",sans-serif;font-weight:400;font-size:11px;color:#444}
.news-date{margin-top:9px;font-family:"Roboto",sans-serif;font-weight:500;font-size:8.5px;color:var(--navy);letter-spacing:.3px}
.news-body p{margin-top:6px;font-size:7.2px;line-height:13.6px;color:#444}
.news-more{margin-top:5px;font-size:8.8px;color:var(--navy);font-weight:600}

/* partners */
.partners{left:0;top:1072px;width:801px;height:62px;background:var(--band)}
.badge{top:22px;height:20px;background:var(--badge);border-radius:3px}

/* footer */
.footer{left:0;top:1134px;width:801px;height:66px;background:var(--navy)}
.footer-links{left:66px;top:17px;font-size:9.6px;color:var(--white)}
.footer-copy{left:66px;top:40px;font-size:7.4px;color:var(--white)}
.social{right:66px;top:27px;display:flex;gap:3px}
.social span{width:16px;height:16px;border:1px solid var(--white);border-radius:50%}
</style>
</head>
<body>

<header>
  <div class="abs brand">
    <span class="brand-mark"></span>
    <span class="brand-name">Varden Recovery, LLC</span>
  </div>
  <div class="abs contact">
    <svg width="20" height="28" viewBox="0 0 20 28" aria-hidden="true"><path d="M5 2c-2 1-3 3-3 6 0 7 5 16 11 18 2 0 4-1 5-3l-4-5-3 2C9 18 7 13 7 10l3-1L9 3z" fill="#c9c9c9"/></svg>
    <div class="contact-text">
      <div>info@vardenrecovery.com</div>
      <div class="toll">Toll Free : 800-555-0182</div>
    </div>
  </div>
</header>

<nav class="abs nav">
  <div class="abs nav-home">
    <svg width="16" height="14" viewBox="0 0 16 14" aria-hidden="true"><path d="M8 0 0 7h2v7h4V9h4v5h4V7h2z" fill="#fff"/></svg>
  </div>
  <span class="abs nav-item" style="left:142px">ABOUT VARDEN</span>
  <span class="abs nav-item" style="left:246px">DEBT COLLECTION</span>
  <span class="abs nav-item" style="left:374px">OUR SERVICES</span>
  <span class="abs nav-item" style="left:486px">RECOVERY</span>
  <span class="abs nav-item" style="left:566px">VARDEN NEWS</span>
  <span class="abs nav-item" style="left:665px">CONTACT US</span>
</nav>

<section>
  <div class="abs hero" role="img" aria-label="Photo of a team of colleagues planning at a glass board"></div>
  <h2 class="abs hero-title">DEBT<br>RECOVERY</h2>
  <span class="abs hero-arrow" style="left:96px"><svg width="8" height="10" viewBox="0 0 8 10"><path d="M6 1 2 5l4 4" stroke="#fff" stroke-width="1.6" fill="none"/></svg></span>
  <span class="abs hero-arrow" style="left:119px"><svg width="8" height="10" viewBox="0 0 8 10"><path d="M2 1l4 4-4 4" stroke="#fff" stroke-width="1.6" fill="none"/></svg></span>
</section>

<section class="abs welcome">
  <h1>Welcome To <strong>Varden Recovery</strong></h1>
  <p>Lorem ipsum dolor sit amet, consectetur adipiscing elit, sed do eiusmod tempor incididunt ut labore et dolore magna aliqua. Ut enim ad minim veniam, quis nostrud exercitation ullamco laboris nisi ut aliquip ex ea commodo consequat. Duis aute irure dolor in reprehenderit in voluptate velit esse cillum dolore eu fugiat nulla pariatur. Excepteur sint occaecat cupidatat non &nbsp;Duis aute irure dolor Duis aute irure dolor in reprehenderit</p>
</section>

<article class="abs service" style="left:66px">
  <div class="service-img" role="img" aria-label="Photo of a large timber family house" style="background:linear-gradient(180deg,#8ea4bf 0%,#b9c3cc 45%,#8a6a4a 75%,#4d5a3c 100%)"></div>
  <h2>RESIDENTIAL</h2>
  <p>Lorem ipsum dolor sit amet, consectetur adipisicing elit, sed do eiusmod tempor incididunt ut labore et dolore magna Lorem ipsum dolor sit amet.</p>
  <a class="read-more">Read More</a>
</article>
<article class="abs service" style="left:298px">
  <div class="service-img" role="img" aria-label="Photo of a tall office tower against a blue sky" style="background:linear-gradient(135deg,#1d3f8a 0%,#3563b0 45%,#dfe6ee 60%,#2b57a3 100%)"></div>
  <h2>COMMERCIAL</h2>
  <p>Lorem ipsum dolor sit amet, consectetur adipisicing elit, sed do eiusmod tempor incididunt ut labore et dolore magna Lorem ipsum dolor sit amet.</p>
  <a class="read-more">Read More</a>
</article>
<article class="abs service" style="left:529px">
  <div class="service-img" role="img" aria-label="Photo of a happy couple in a red car" style="background:linear-gradient(90deg,#c8344a 0%,#d9a08c 45%,#8fae6a 80%,#5f8a3f 100%)"></div>
  <h2>AUTOMOBILE</h2>
  <p>Lorem ipsum dolor sit amet, consectetur adipisicing elit, sed do eiusmod tempor incididunt ut labore et dolore magna Lorem ipsum dolor sit amet.</p>
  <a class="read-more">Read More</a>
</article>

<div class="abs divider"></div>

<h2 class="abs news-heading">LATEST NEWS</h2>
<div class="abs news-img" style="left:66px" role="img" aria-label="Photo of a couple receiving car keys from a dealer" style="background:#777"></div>
<div class="abs news-img" style="left:66px;background:linear-gradient(90deg,#cfd3d6 0%,#3a3a3a 35%,#e8e8e8 60%,#2f2f2f 100%)" aria-hidden="true"></div>
<article class="abs news-body" style="left:207px">
  <h3>Nulla at diam ornare, aliquam urna</h3>
  <div class="news-date">FEB 25, 2015</div>
  <p>Nulla at diam ornare, aliquam urna vel, commodo urna. Nam id risus a est luctus consectetur quis eget libero. Suspendisse potenti. Pellentesque habitant morbi tristique senectus</p>
  <div class="news-more">Read More +</div>
</article>
<div class="abs news-img" style="left:420px;background:linear-gradient(90deg,#dfe4e8 0%,#a89a8a 40%,#e9eef2 60%,#4a79b8 100%)" role="img" aria-label="Photo of two colleagues reviewing documents at a desk"></div>
<article class="abs news-body" style="left:562px">
  <h3>Nulla at diam ornare, aliquam urna</h3>
  <div class="news-date">FEB 25, 2015</div>
  <p>Nulla at diam ornare, aliquam urna vel, commodo urna. Nam id risus a est luctus consectetur quis eget libero. Suspendisse potenti. Pellentesque habitant morbi tristique senectus</p>
  <div class="news-more">Read More +</div>
</article>

<section class="abs partners" aria-label="Partners">
  <span class="abs badge" style="left:88px;width:42px"></span>
  <span class="abs badge" style="left:169px;width:74px"></span>
  <span class="abs badge" style="left:284px;width:72px"></span>
  <span class="abs badge" style="left:393px;width:72px"></span>
  <span class="abs badge" style="left:522px;width:54px"></span>
  <span class="abs badge" style="left:625px;width:77px"></span>
</section>

<footer class="abs footer">
  <div class="abs footer-links">Home &nbsp;/&nbsp; About Us &nbsp;/&nbsp; Services &nbsp;/&nbsp; Debt Collection &nbsp;/&nbsp; Contact Us</div>
  <div class="abs footer-copy">©2014 - 2015 &nbsp;Varden Recovery , All Rights Reserved.</div>
  <div class="abs social" aria-label="Social links"><span></span><span></span><span></span><span></span><span></span></div>
</footer>

</body>
</html>
```